Verlindo Magician

I want the business card for my business to give to people who watch that later I will be employed to show magic here is my website http://www.verlindoillusions.example/I want the interesting design , i am very opened for formal and informal, I watch a lot of design so don't stick to the common shape and form but i hope it can also be produced the thing to write on will be the same as in picture that i will upload , i also will upload the logo for you that so can be easy to useDenis CostilleMagicianMAGICIAN BALSAMO 17 rue des Tilleuls - 25000 BESANÇON contact@verlindoillusions.example tel. 0381 946 157 tel. 0674 219 503

```html
<!DOCTYPE html>
<html lang="en">
<head>
<meta charset="utf-8">
<title>Verlindo Magician – Business Card</title>
<link href="https://fonts.googleapis.com/css2?family=Jost:wght@300;400&display=swap" rel="stylesheet">
<style>
  :root {
    --backdrop: #3a3a3a;
    --card: #ffffff;
    --ink: #111111;
    --muted: #555555;
    --accent: #e8262b;
    --figure: #1a1a1a;
  }
  * { box-sizing: border-box; margin: 0; padding: 0; }
  html, body { width: 1200px; height: 960px; overflow: hidden; }
  body {
    background: radial-gradient(ellipse at 50% 50%, #5a5a5a 0%, var(--backdrop) 70%);
    font-family: "Jost", "Futura", sans-serif;
    font-weight: 300;
    color: var(--ink);
    position: relative;
  }
  .card {
    position: absolute;
    background: var(--card);
    box-shadow: 0 14px 30px rgba(0,0,0,0.45);
  }
  /* Logo side */
  .card--logo { left: 80px; top: 70px; width: 600px; height: 343px; }
  .card--logo .figure {
    position: absolute; left: 245px; top: 48px; width: 110px; height: 125px;
    background: var(--figure); border-radius: 40px 40px 8px 8px;
  }
  .card--logo .wordmark {
    position: absolute; left: 0; right: 0; top: 186px; text-align: center;
    font-size: 24px; letter-spacing: 1px; color: var(--ink);
  }
  .card--logo .site {
    position: absolute; left: 0; right: 0; bottom: 40px; text-align: center;
    font-size: 13px; letter-spacing: 2px; color: var(--muted);
  }
  /* Details side */
  .card--details { left: 500px; top: 440px; width: 660px; height: 377px; }
  .card--details .figure {
    position: absolute; right: 44px; top: 34px; width: 250px; height: 300px;
    background: var(--figure); border-radius: 110px 110px 12px 12px;
  }
  .card--details .wordmark {
    position: absolute; left: 40px; top: 60px;
    font-size: 34px; letter-spacing: 1px; color: var(--ink);
  }
  .person { position: absolute; left: 40px; top: 148px; }
  .person__name { font-size: 22px; font-weight: 400; }
  .person__role { font-size: 17px; color: var(--accent); margin-top: -2px; }
  .address {
    position: absolute; left: 40px; top: 210px;
    font-size: 13px; line-height: 17px; color: var(--muted); letter-spacing: 0.3px;
  }
  .contacts { position: absolute; left: 40px; top: 256px; list-style: none; }
  .contacts li {
    display: flex; align-items: center; gap: 8px;
    font-size: 13px; line-height: 19px; color: var(--muted);
  }
  .contacts svg { width: 12px; height: 12px; fill: var(--ink); flex: none; }
</style>
</head>
<body>

<section class="card card--logo">
  <div class="figure" role="img" aria-label="Black and white illustration of the magician holding a playing card"></div>
  <div class="wordmark">Verlindo Magician</div>
  <div class="site">www.verlindoillusions.example</div>
</section>

<section class="card card--details">
  <div class="wordmark">Verlindo Magician</div>
  <div class="person">
    <div class="person__name">Marc Ravoulet</div>
    <div class="person__role">Magician</div>
  </div>
  <div class="address">
    MAGICIAN VERLINDO<br>
    17 rue des Tilleuls - 25000 BESANÇON
  </div>
  <ul class="contacts">
    <li><svg viewBox="0 0 12 12"><path d="M2.5 0.5 L4.5 0.5 L5 3.5 L3.6 4.4 Q4.6 6.9 7.6 8.4 L8.5 7 L11.5 7.5 L11.5 9.5 Q11 11.5 9 11.5 Q1 10.5 0.5 3 Q0.5 1 2.5 0.5Z"/></svg>0381 946 157</li>
    <li><svg viewBox="0 0 12 12"><path d="M2.5 0.5 L4.5 0.5 L5 3.5 L3.6 4.4 Q4.6 6.9 7.6 8.4 L8.5 7 L11.5 7.5 L11.5 9.5 Q11 11.5 9 11.5 Q1 10.5 0.5 3 Q0.5 1 2.5 0.5Z"/></svg>0674 219 503</li>
    <li><svg viewBox="0 0 12 12"><path d="M0.5 2 H11.5 V10 H0.5Z M1.2 2.6 L6 6.6 L10.8 2.6" fill="none" stroke="#111" stroke-width="1.1"/></svg>contact@verlindoillusions.example</li>
    <li><svg viewBox="0 0 12 12"><circle cx="6" cy="6" r="5.3" fill="none" stroke="#111" stroke-width="1.1"/><path d="M0.7 6 H11.3 M6 0.7 Q2.8 6 6 11.3 M6 0.7 Q9.2 6 6 11.3" fill="none" stroke="#111" stroke-width="0.9"/></svg>www.verlindoillusions.example</li>
  </ul>
  <div class="figure" role="img" aria-label="Large black and white illustration of the magician presenting a playing card"></div>
</section>

</body>
</html>
```